New Company Business Card design

Looking for a corporate looking business card utilising my new logo design - the logo i would like embossed as one option and flat as another - simplistic but stylish - less is more - we are an import export business launching into the market - i would like a couple of options as main background - Grey or Black

```html
<!DOCTYPE html>
<html lang="en">
<head>
<meta charset="utf-8">
<title>Meridian Trade Partners – Business Card</title>
<link href="https://fonts.googleapis.com/css2?family=Cinzel:wght@400;500&family=Arimo:wght@400;700&display=swap" rel="stylesheet">
<style>
  :root {
    --stage: #2b2b2b;
    --card-light: #f3f3f3;
    --brand-blue: #0a72c4;
    --ink: #1a1a1a;
    --muted-grey: #6b6b6b;
    --rule: #8a8a8a;
    --white: #ffffff;
  }
  * { margin: 0; padding: 0; box-sizing: border-box; }
  html, body { width: 1200px; height: 1200px; overflow: hidden; }
  body { background: var(--stage); position: relative; font-family: "Arimo", Arial, sans-serif; }

  .card { position: absolute; top: 310px; height: 594px; box-shadow: 0 3px 8px rgba(0,0,0,.45); }
  .card-front { left: 234px; width: 364px; background: var(--card-light); text-align: center; }
  .card-back { left: 627px; width: 369px; background: var(--brand-blue); text-align: center; }

  .brand-mark { position: absolute; left: 50%; transform: translateX(-50%); border-radius: 50%; }
  .card-front .brand-mark { top: 92px; width: 92px; height: 92px; background: var(--brand-blue); }
  .brand-name {
    position: absolute; left: 0; right: 0;
    font-family: "Cinzel", "Times New Roman", serif; font-weight: 500;
    line-height: 1.1; letter-spacing: 0.5px; white-space: nowrap;
  }
  .card-front .brand-name { top: 207px; font-size: 21px; color: var(--brand-blue); }

  .person-name {
    position: absolute; left: 0; right: 0; top: 322px;
    font-family: "Cinzel", "Times New Roman", serif; font-size: 26px; font-weight: 400;
    line-height: 30px; color: var(--brand-blue); letter-spacing: 0.6px;
  }
  .person-name .surname { color: var(--muted-grey); }
  .person-title { position: absolute; left: 0; right: 0; top: 348px; font-size: 17px; line-height: 20px; color: var(--ink); }

  .rule { position: absolute; left: 78px; width: 208px; height: 1px; background: var(--rule); }
  .rule-top { top: 380px; }
  .rule-bottom { top: 493px; }

  .contact-list { position: absolute; left: 0; right: 0; top: 394px; list-style: none; font-size: 17px; line-height: 21.7px; color: var(--ink); }
  .contact-list .label { color: var(--brand-blue); font-weight: 700; }
  .contact-list .web { color: var(--brand-blue); font-weight: 700; }

  .address { position: absolute; left: 0; right: 0; top: 512px; font-size: 17px; line-height: 21px; color: var(--ink); font-style: normal; }

  .card-back .brand-mark { top: 186px; width: 110px; height: 110px; background: var(--white); }
  .card-back .brand-name { top: 318px; font-size: 33px; line-height: 38px; color: var(--white); }
  .web-footer {
    position: absolute; left: 0; right: 0; top: 527px;
    font-family: "Cinzel", "Times New Roman", serif; font-size: 17px; color: var(--white); letter-spacing: 1.6px;
  }
</style>
</head>
<body>
  <section class="card card-front">
    <div class="brand-mark"></div>
    <div class="brand-name">Meridian Trade Partners</div>

    <div class="person-name">Daniel <span class="surname">Harper</span></div>
    <div class="person-title">Managing Director</div>
    <div class="rule rule-top"></div>

    <ul class="contact-list">
      <li><span class="label">P:</span> 055-210 348 671</li>
      <li><span class="label">M:</span> 055-210 348 671</li>
      <li><span class="label">E:</span> info@meridiantrade.com</li>
      <li class="web">www.meridiantrade.com</li>
    </ul>

    <div class="rule rule-bottom"></div>
    <address class="address">12345, Address Goes Here<br>Country Name, 123456.</address>
  </section>

  <section class="card card-back">
    <div class="brand-mark"></div>
    <div class="brand-name">Meridian<br>Trade Partners</div>
    <div class="web-footer">WWW.MERIDIANTRADE.COM</div>
  </section>
</body>
</html>
```